We need UI/UX design for a public, informational website for The Copper Lantern.
The pages, structure, and content scope are already defined. Designers are required to work only on the UI/UX layout of these existing pages, focusing on clarity, hierarchy, spacing, and usability. Do not add, remove, rename, or reinterpret pages or content.
The website is strictly informational only. It must not include accounts, onboarding, payments, custody, escrow administration, marketplaces, dashboards, or any transactional functionality.
Scope of work
Apply UI/UX design to the predefined website pages
Design layout for text, images, notices, and sections
Ensure consistent components and layout patterns across page types
Optimize layouts for long form, compliance focused content
Content writing, page creation, and branding changes are out of scope.
Structure reference
The complete page list, hierarchy, and content definitions are provided in the technical documentation and must be treated as the primary source of truth.
A Figma link is provided only as a light visual reference for page existence and structure:
https://meadow-knot-48203956.plumsite.example/
Designers must rely on the documentation for in depth and authoritative reference.
Brand guidelines
The Copper Lantern has existing brand guidelines and official logos, including light and dark versions. These assets will be provided and must be followed exactly. Designers must not redesign, alter, or reinterpret the brand identity.
Look and feel direction
The desired visual direction is inspired by:
https://ledgerwaltz.example/
This reference is provided only to indicate:
Institutional and enterprise tone
Clean, modern typography
Strong hierarchy and generous whitespace
Editorial, content first layouts
Do not copy branding, layouts, components, or assets from the reference site.
Hero section direction
The hero section should follow a similar structural approach to the hero used on https://ledgerwaltz.example/
, meaning:
Strong editorial framing
Clear headline hierarchy
Calm, institutional first impression
However, the background video must be Abu Dhabi focused, not generic or global. The video should visually reflect:
Abu Dhabi skyline or architectural language
Institutional, sovereign, long term infrastructure tone
Clean, slow, cinematic motion
No promotional, marketing, or lifestyle visuals
The hero must remain informational, restrained, and credible. No hype. No calls to invest. No implied participation.
Constraints
One global primary CTA only: “Continue to Halvemark” (external)
All other interactions must be informational
No visuals or language implying offers, investment, eligibility, or participation
Clear separation between informational content and any external operational platforms
Deliverables
High fidelity UI/UX designs created in Figma, covering:
Desktop layouts
Tablet layouts where relevant
Mobile layouts
Complete Figma file(s) including:
All designed pages defined in the technical documentation
A reusable component library (headers, footers, cards, notice panels, forms, CTAs, typography styles, spacing system)
Clearly defined layout grids, spacing rules, and text styles
Proper use of components and variants, not detached frames
Designs prepared for developer handoff, including:
Clear layer naming and structure
Auto layout where appropriate
Consistent use of styles and components
Responsive behavior demonstrated within Figma
Notes or annotations only where necessary for clarity
No prototypes, interactions, or motion design beyond basic layout states, unless explicitly requested. The focus is static UI/UX clarity, not animation.
A detailed technical specification document and official brand assets will be provided.
Any designs delivered outside Figma, that alter structure or content, or that ignore the defined constraints, boundaries, or tone will be rejected.

```html
<!DOCTYPE html>
<html lang="en">
<head>
<meta charset="utf-8">
<title>The Copper Lantern</title>
<link href="https://fonts.googleapis.com/css2?family=Lexend:wght@300;400;500;600;700&display=swap" rel="stylesheet">
<style>
:root{
  --navy:#0b1a33;
  --navy-deep:#07111f;
  --card:#10254a;
  --cyan:#2ad3f0;
  --blue:#4db4f6;
  --violet:#a27ef6;
  --button:#a884f6;
  --ink:#2a2f3a;
  --white:#ffffff;
  --muted:#dfe6f3;
}
*{box-sizing:border-box;margin:0;padding:0}
html,body{width:1200px;height:3852px;overflow:hidden}
body{font-family:"Lexend",sans-serif;color:var(--ink);background:var(--white);position:relative}
.abs{position:absolute}
.grad{background:linear-gradient(90deg,var(--blue),var(--violet));-webkit-background-clip:text;background-clip:text;color:transparent;font-weight:700;letter-spacing:-0.5px}
.rule{width:38px;height:3px;background:var(--cyan)}
.btn{display:inline-flex;align-items:center;justify-content:center;background:var(--button);color:var(--white);border-radius:24px;font-size:14px;font-weight:400;text-transform:uppercase;letter-spacing:.2px}
.body-text{font-size:16px;line-height:34.4px;text-align:justify}

/* header */
.site-header{left:0;top:0;width:1200px;height:68px;background:var(--navy);z-index:3}
.brand{left:104px;top:12px;display:flex;align-items:center;gap:10px;color:var(--white);font-size:17px;font-weight:500;letter-spacing:.5px;text-transform:uppercase}
.brand-mark{width:18px;height:18px;border-radius:50%;border:2px solid var(--cyan)}
.nav{left:450px;top:26px;display:flex;gap:30px;font-size:13px;color:var(--white);text-transform:uppercase}
.nav .active{color:var(--cyan)}
.caret::after{content:"▾";font-size:9px;margin-left:5px}

/* hero */
.hero{left:0;top:68px;width:1200px;height:444px;border-radius:0 0 140px 0;overflow:hidden;background:linear-gradient(90deg,#eef3f8 0%,#e3ecf4 40%,#b9cfe0 70%,#8aa8c2 100%)}
.hero-title{left:112px;top:78px;font-size:32px}
.hero-copy{left:112px;top:138px;width:460px;font-size:16px;line-height:34.4px;color:#1d2433}
.hero .btn{left:112px;top:264px;width:224px;height:46px}

/* image blocks */
.photo{overflow:hidden}
.frame{border:2px solid var(--cyan)}

/* band */
.band{left:0;width:1200px;background:var(--navy);border-radius:60px 60px 0 0;color:var(--white)}
.center{left:0;width:1200px;text-align:center}
.card{background:var(--card);border-radius:6px;width:296px;height:356px}
.card-tab{left:0;top:22px;width:82px;height:58px;border-radius:0 29px 29px 0;display:flex;align-items:center;justify-content:center}
.card h3{position:absolute;left:21px;top:106px;font-size:18px}
.card p{position:absolute;left:21px;top:148px;width:260px;font-size:16px;line-height:34.4px;color:var(--white)}
.outline-btn{position:absolute;left:21px;top:280px;width:128px;height:42px;border:1.5px solid var(--cyan);border-radius:22px;color:var(--cyan);font-size:13px;display:flex;align-items:center;justify-content:center;text-transform:uppercase}
.card.purple .outline-btn{border-color:var(--violet);color:var(--violet)}

/* footer */
.site-footer{left:0;top:3460px;width:1200px;height:392px;background:var(--navy-deep);color:var(--white)}
.foot-brand{left:118px;top:68px;font-size:22px}
.foot-col{top:52px}
.foot-col h4{font-size:20px;margin-bottom:20px}
.foot-col li{list-style:none;font-size:15px;line-height:34.4px}
</style>
</head>
<body>

<header class="site-header abs">
  <div class="brand abs" style="top:36px;transform:translateY(-50%)"><span class="brand-mark"></span>The Copper Lantern</div>
  <nav class="nav abs">
    <span class="active">Home</span>
    <span class="caret">Framework</span>
    <span>Projects</span>
    <span>Halvemark</span>
    <span>Insights</span>
    <span class="caret">Company</span>
    <span class="caret">Contact</span>
  </nav>
</header>

<section class="hero abs">
  <div class="abs" role="img" aria-label="Abu Dhabi skyline with tall glass towers beside the sea" style="left:560px;top:0;width:640px;height:444px;background:linear-gradient(180deg,#cfdbe6 0%,#7f9db8 45%,#5d7b95 75%,#a99a83 100%);opacity:.85"></div>
  <h1 class="hero-title abs grad">The Copper Lantern</h1>
  <p class="hero-copy abs">The Copper Lantern is a governance and project origination group. Its purpose is to define structural standards and oversight principles for complex initiatives.</p>
  <a class="btn abs">Continue to Halvemark</a>
</section>

<section class="intro">
  <div class="frame abs" style="left:140px;top:620px;width:444px;height:460px;border-radius:0 230px 0 0;border-left:none;border-top:none"></div>
  <div class="photo abs" role="img" aria-label="Abu Dhabi waterfront towers and marina" style="left:112px;top:600px;width:472px;height:476px;border-radius:0 238px 238px 238px;background:linear-gradient(160deg,#d9e3ec 0%,#8ea6bc 45%,#6b7f8f 70%,#4f7f83 100%)"></div>
  <h2 class="abs grad" style="left:657px;top:586px;width:440px;font-size:30px;line-height:47px">Governance and Project Origination</h2>
  <div class="rule abs" style="left:657px;top:702px"></div>
  <p class="body-text abs" style="left:657px;top:733px;width:432px">Governance in this context refers to the standards that determine how projects are structured and how oversight is described. Origination refers to the initial design and definition of an initiative, including role separation, reporting expectations, and boundary setting before execution begins. The Copper Lantern focuses on these governance-level elements rather than on operating day-to-day workflows.</p>
  <a class="btn abs" style="left:657px;top:1038px;width:148px;height:46px">Learn More</a>
</section>

<section class="band abs" style="top:1170px;height:746px">
  <h2 class="abs center grad" style="top:50px;font-size:30px">How the Ecosystem Works</h2>
  <div class="rule abs" style="left:581px;top:111px;width:48px"></div>
  <p class="abs center" style="top:152px;font-size:16px">At a high level, the ecosystem can be understood as three layers:</p>

  <div class="card abs" style="left:112px;top:227px">
    <div class="card-tab abs" style="background:var(--cyan)">
      <svg width="40" height="40" viewBox="0 0 40 40" fill="none" stroke="#fff" stroke-width="2"><path d="M6 16 20 8l14 8H6z"/><path d="M10 16v14M16 16v14M24 16v14M30 16v14M5 32h30"/></svg>
    </div>
    <h3 class="grad">Governance</h3>
    <p>defines standards, explains role boundaries, and publishes framework information</p>
    <span class="outline-btn">Read More</span>
  </div>
  <div class="card abs" style="left:452px;top:227px">
    <div class="card-tab abs" style="background:var(--blue)">
      <svg width="40" height="40" viewBox="0 0 40 40" fill="none" stroke="#fff" stroke-width="2"><circle cx="20" cy="14" r="6"/><circle cx="20" cy="14" r="2"/><circle cx="10" cy="24" r="3"/><circle cx="30" cy="24" r="3"/><path d="M5 34c0-4 2-6 5-6s5 2 5 6M25 34c0-4 2-6 5-6s5 2 5 6M14 34c0-5 3-8 6-8s6 3 6 8"/></svg>
    </div>
    <h3 class="grad">Operations</h3>
    <p>manages workflow processes such as documentation steps and record-anchored audit</p>
    <span class="outline-btn">Read More</span>
  </div>
  <div class="card purple abs" style="left:793px;top:227px">
    <div class="card-tab abs" style="background:var(--violet)">
      <svg width="40" height="40" viewBox="0 0 40 40" fill="none" stroke="#fff" stroke-width="2"><circle cx="20" cy="18" r="11"/><circle cx="20" cy="18" r="4"/><path d="M20 7v4M20 25v4M9 18h4M27 18h4M26 28l6 6"/></svg>
    </div>
    <h3 class="grad">Project Execution</h3>
    <p>occurs at the project level through dedicated structures that hold responsibilities</p>
    <span class="outline-btn">Read More</span>
  </div>

  <p class="abs center" style="top:628px;font-size:16px;line-height:34.4px">This website focuses on the governance layer and provides links to learn about structural concepts such as<br>role separation, escrow and milestone framing, and recordkeeping terminology</p>
</section>

<section class="roles">
  <h2 class="abs grad" style="left:118px;top:2002px;font-size:30px">Clear Role Separation</h2>
  <div class="rule abs" style="left:118px;top:2065px"></div>
  <p class="body-text abs" style="left:118px;top:2090px;width:430px">The ecosystem is designed around clear separation of responsibilities. Governance activities belong at the framework layer. Operational workflows, where available, belong on a separate operating platform designed for process execution and recordkeeping. Assets and project execution, where applicable, belong at the project level through ring-fenced structures created for specific initiatives. This separation is intended to reduce ambiguity and help stakeholders understand who is responsible for what.</p>
  <div class="frame abs" style="left:652px;top:2002px;width:428px;height:434px;border-radius:0 0 0 217px;border-top:none;border-right:none"></div>
  <div class="photo abs" role="img" aria-label="Two colleagues in business attire reviewing notes at a table" style="left:652px;top:2000px;width:430px;height:430px;border-radius:215px 0 215px 215px;background:linear-gradient(135deg,#eae6e0 0%,#c9c2b8 45%,#8e8a86 75%,#5e5a58 100%)"></div>

  <div class="frame abs" style="left:112px;top:2527px;width:428px;height:430px;border-radius:0 0 215px 0;border-top:none;border-left:none"></div>
  <div class="photo abs" role="img" aria-label="Hands working on a laptop with floating business icons for goals and growth" style="left:112px;top:2522px;width:428px;height:430px;border-radius:215px 215px 215px 0;background:linear-gradient(135deg,#1b3a78 0%,#2f5fa8 40%,#7da0c9 70%,#c9d4de 100%)"></div>
  <h2 class="abs grad" style="left:649px;top:2532px;width:440px;font-size:30px;line-height:47px">Independent Escrow and Milestone Oversight</h2>
  <div class="rule abs" style="left:649px;top:2640px"></div>
  <p class="abs" style="left:649px;top:2666px;width:434px;font-size:16px;line-height:34.4px">Some initiatives use independent escrow arrangements to coordinate staged releases linked to milestone completion. Escrow can support execution discipline by requiring defined evidence before releases occur. Escrow does not guarantee outcomes, timelines, or success, and it is not administered by this website operator. This site describes the concept for clarity and transparency.</p>
</section>

<section class="band abs" style="top:3040px;height:420px">
  <h2 class="abs center grad" style="top:84px;font-size:30px">Where Operational Workflows Happen</h2>
  <div class="rule abs" style="left:581px;top:133px;width:40px"></div>
  <p class="abs center" style="top:170px;font-size:16px;line-height:34.4px">Operational workflows, including any onboarding or workflow participation where permitted, occur on a<br>separate operating platform under separate terms and policies. If you need operational access, use the<br>Halvemark page on this site to navigate externally. This website does not host those workflows.</p>
  <a class="btn abs" style="left:526px;top:308px;width:148px;height:46px">Learn More</a>
</section>

<footer class="site-footer abs">
  <div class="foot-brand abs brand" style="left:118px;top:56px;font-size:22px"><span class="brand-mark" style="width:22px;height:22px"></span>The Copper Lantern</div>
  <p class="abs" style="left:118px;top:192px;font-size:14px;line-height:29px">© 2026 The Copper Lantern.<br>All rights reserved</p>
  <div class="foot-col abs" style="left:457px">
    <h4 class="grad">Quick Links</h4>
    <ul><li>Framework</li><li>Projects</li><li>Halvemark</li><li>Insights</li><li>Company</li><li>Contact</li><li>Glossary</li></ul>
  </div>
  <div class="foot-col abs" style="left:688px">
    <h4 class="grad">Company</h4>
    <ul><li>About</li><li>Leadership</li><li>Governance</li><li>Press</li><li>Careers</li><li>Contact</li></ul>
  </div>
  <div class="foot-col abs" style="left:897px">
    <h4 class="grad">Legal</h4>
    <ul><li>Legal (Index)</li><li>Terms of Use</li><li>Privacy Policy</li><li>Cookie Policy</li><li>Disclaimer &amp; Risk Notices</li><li>Acceptable Use Policy</li><li>Accessibility Statement</li></ul>
  </div>
</footer>

</body>
</html>
```